Event Center Website

We need a new website design for an upscale event center in Reno, Nevada. The building hosts everything from weddings to corporate events to funerals and it competitively more expensive. The overall look and feel is consistent with a Lake Tahoe aesthetic. The current site can be viewed at www.themaplehallevents.com. They are looking for a major upgrade. A sample site they like is www.cliffsidelodgestay.com. We have new photography available (some attached). The site should be very visual. A site map is attached as well for direction on what elements the site should include as well as labels for navigation. I am looking for a home page and sample interior page. Any questions, let me know. Thanks.
Updates

I have added some photography of the center itself for use rather than stock photography. Thanks!

Target Market(s)

Brides, professionals, high-income

Industry/Entity Type

Building

Requirements
Must have
• See site map

```html
<!DOCTYPE html>
<html lang="en">
<head>
<meta charset="utf-8">
<title>Maple Hall at Cedar Ridge</title>
<link href="https://fonts.googleapis.com/css2?family=Open+Sans:wght@400;600&family=Roboto+Condensed:wght@400;700&family=Parisienne&display=swap" rel="stylesheet">
<style>
:root{
  --header:#5a3a22;
  --nav-text:#ffffff;
  --dropdown:#d39a74;
  --dropdown-line:#e9bea0;
  --band:rgba(40,34,30,.72);
  --accent:#dba17c;
  --blush:#fde0d6;
  --footer-dark:#4a3220;
  --orange:#f47c06;
  --white:#ffffff;
}
*{box-sizing:border-box;margin:0;padding:0}
html,body{width:1178px;height:1200px;overflow:hidden}
body{position:relative;font-family:"Open Sans",sans-serif;background:var(--blush)}
.hero-photo{position:absolute;left:0;top:0;width:1178px;height:730px;
  background:linear-gradient(180deg,#6b4a2e 0%,#8a6a45 18%,#7d8a55 35%,#a28c6e 48%,#8b7358 62%,#5b4535 100%)}
.site-header{position:absolute;left:0;top:0;width:1178px;height:108px;background:rgba(90,58,34,.9)}
.brand{position:absolute;left:123px;top:28px;height:60px;display:flex;align-items:center;gap:10px;
  background:var(--header);padding:0 12px 0 0}
.brand-mark{width:66px;height:60px;background:var(--white)}
.brand-name{font-family:"Open Sans",sans-serif;font-weight:400;font-size:22px;color:var(--white)}
.main-nav{position:absolute;left:494px;top:62px;display:flex;gap:19px;
  font-family:"Roboto Condensed",sans-serif;font-weight:700;font-size:14.5px;color:var(--nav-text)}
.dropdown{position:absolute;left:533px;top:108px;width:102px;background:var(--dropdown)}
.dropdown li{list-style:none;height:35.5px;line-height:35px;padding-left:18px;font-size:12.5px;color:var(--white);
  border-bottom:1px solid var(--dropdown-line)}
.dropdown li:last-child{border-bottom:none}
.intro-band{position:absolute;left:0;top:519px;width:1178px;height:198px;background:var(--band);text-align:center}
.intro-text{position:absolute;left:150px;top:35px;width:960px;font-family:"Parisienne",cursive;font-size:21px;line-height:31px;color:var(--white)}
.btn-appointment{position:absolute;left:523px;top:139px;width:185px;height:38px;border-radius:3px;background:var(--accent);
  font-size:14px;font-weight:600;line-height:38px;color:#3a2616}
.gallery{position:absolute;left:0;top:730px;width:1178px;height:280px;background:var(--blush)}
.thumb{position:absolute;top:67px;height:158px}
.thumb.active{border:3px solid var(--white)}
.t1{left:122px;width:212px;background:linear-gradient(180deg,#c98a8a,#8a7060 55%,#c9a48f)}
.t2{left:363px;width:201px;top:69px;height:154px;background:linear-gradient(180deg,#c98a8a,#8a7060 55%,#c9a48f)}
.t3{left:604px;width:211px;top:69px;height:155px;background:linear-gradient(160deg,#8a5a4e,#d49a9a 40%,#9aa27a 75%,#d8d8d0)}
.t4{left:843px;width:212px;top:69px;height:155px;background:linear-gradient(180deg,#6b5234,#d8cfc0 35%,#3d342c 60%,#e8e2dc)}
.arrow{position:absolute;top:122px}
.site-footer{position:absolute;left:0;top:1010px;width:1178px;height:190px;
  background:linear-gradient(180deg,#6a4a30 0%,#7f6b4d 35%,#6f5a44 70%,#5a4230 100%);color:var(--white)}
.col-title{position:absolute;top:26px;font-size:21px;font-weight:400}
.contact-lines{position:absolute;left:122px;top:76px;font-size:13px;line-height:23px}
.contact-lines strong{font-weight:600;font-size:14px}
.reach{position:absolute;left:363px;top:70px;width:200px;font-size:16px;font-weight:600;line-height:30px;white-space:nowrap}
.reach div{display:flex;align-items:center;gap:9px}
.field{position:absolute;top:72px;height:33px;border:2px solid rgba(255,255,255,.35);border-radius:2px;
  background:rgba(110,90,70,.35);font-size:10.5px;padding:8px 10px;color:#f3ece4}
.btn-get{position:absolute;left:577px;top:127px;width:158px;height:32px;background:var(--orange);
  font-size:10.5px;font-weight:600;line-height:32px;text-align:center;color:var(--white)}
</style>
</head>
<body>
<div class="hero-photo" role="img" aria-label="Event hall interior with draped cocktail tables, a loveseat and open doors to a garden patio"></div>

<header class="site-header">
  <div class="brand"><span class="brand-mark"></span><span class="brand-name">Maple Hall</span></div>
  <nav class="main-nav">
    <span>HOME</span><span>ABOUT US</span><span>GALLERY</span><span>WEDDINGS</span><span>MEETINGS</span><span>OTHER EVENTS</span><span>CATERINGS</span>
  </nav>
</header>
<ul class="dropdown">
  <li>Nora Bio</li><li>Delia Bio</li><li>Marlow Bio</li><li>Everett Bio</li>
</ul>

<section class="intro-band">
  <p class="intro-text">Maple Hall is Reno's newest, most elegant special events center. Our onsite staff and catering department can assist you in planning the event you desire. From wedding receptions and ceremonies to business meetings or any other special occasion, we offer full service event planning and catering to create a truly unique and memorable experience.</p>
  <div class="btn-appointment">Schedual an appointment</div>
</section>

<section class="gallery">
  <svg class="arrow" style="left:64px" width="16" height="26" viewBox="0 0 16 26"><path d="M13 2 3 13l10 11" fill="none" stroke="#3a2a22" stroke-width="2.5"/></svg>
  <div class="thumb t1 active" role="img" aria-label="Dining table with pink drapes and floral arch"></div>
  <div class="thumb t2" role="img" aria-label="Dining table with pink drapes and floral arch"></div>
  <div class="thumb t3" role="img" aria-label="Close view of a floral arrangement by a window"></div>
  <div class="thumb t4" role="img" aria-label="Ceremony hall with white chairs and draped ceiling"></div>
  <svg class="arrow" style="left:1097px" width="16" height="26" viewBox="0 0 16 26"><path d="M3 2l10 11L3 24" fill="none" stroke="#3a2a22" stroke-width="2.5"/></svg>
</section>

<footer class="site-footer">
  <h3 class="col-title" style="left:122px">Contact Us</h3>
  <div class="contact-lines"><strong>Maple Hall | Cedar Ridge</strong><br>&nbsp;1820 Larkspur Rd, Suite B<br>Reno, Nevada 89511</div>
  <h3 class="col-title" style="left:363px">Reach Us</h3>
  <div class="reach">
    <div><svg width="17" height="12" viewBox="0 0 17 12"><rect width="17" height="12" rx="1" fill="#f3ece4"/><path d="M0 1l8.5 6L17 1" fill="none" stroke="#7a6048" stroke-width="1.4"/></svg>info@maplehall.com</div>
    <div><svg width="17" height="17" viewBox="0 0 17 17"><rect width="17" height="17" rx="3" fill="#f3ece4"/><path d="M5 3.5c-1 1-1 3 1 5.5s4.5 3.5 5.8 2.3l.8-1-2-1.6-1 .8c-1-.5-2.2-1.8-2.6-2.7l.8-1-1.5-2z" fill="#7a6048"/></svg>+1.555.014.2290</div>
  </div>
  <h3 class="col-title" style="left:576px">Schedule an Appintment</h3>
  <div class="field" style="left:576px;width:160px">Arrival Date</div>
  <div class="field" style="left:750px;width:159px">Adults</div>
  <div class="field" style="left:922px;width:159px">Departual date</div>
  <div class="btn-get">Get an&nbsp; Appointment</div>
</footer>
</body>
</html>
```